Medical VIP club - small design

Please read the specs in a design brief attached. Also we don't have logo in a Vector format and attaching the only version we have.

Club

```html
<!DOCTYPE html>
<html lang="en">
<head>
<meta charset="utf-8">
<title>Carevita — Medical VIP Club</title>
<link rel="stylesheet" href="https://fonts.googleapis.com/css2?family=Cinzel:wght@400;700&family=Cinzel+Decorative:wght@700&family=Marcellus&family=Open+Sans:wght@400;600;700&family=Questrial&display=swap">
<style>
:root{
  --stripe-a:#d9cba2;
  --stripe-b:#e6dab7;
  --page:#f3ecdc;
  --nav:#e2d5b3;
  --nav-text:#6b5b45;
  --heading:#7a6a55;
  --body:#6e6456;
  --accent:#d2381c;
  --hero:#d8462a;
  --hero-dark:#b8361d;
  --sidebar:#e9dfc6;
  --rule:#c9b994;
  --white:#ffffff;
}
*{box-sizing:border-box;margin:0;padding:0}
html,body{width:1200px;height:1052px;overflow:hidden}
body{
  background:repeating-linear-gradient(90deg,var(--stripe-a) 0 22px,var(--stripe-b) 22px 44px);
  font-family:"Open Sans",sans-serif;
}
.stage{width:1300px;height:1140px;position:relative;transform:scale(0.923077);transform-origin:0 0}
.page{position:absolute;left:150px;top:0;width:1000px;height:1140px;background:var(--page);box-shadow:0 0 14px rgba(90,70,30,.25)}
.abs{position:absolute}

/* header */
.brand{left:32px;top:52px;display:flex;align-items:center;gap:10px}
.brand-dot{width:30px;height:30px;border-radius:50%;background:var(--accent)}
.brand-name{font-family:"Open Sans",sans-serif;font-weight:700;font-size:38px;color:var(--accent);line-height:1}
.brand-tag{left:74px;top:94px;font-family:"Open Sans",sans-serif;font-weight:700;font-size:12px;color:var(--accent);letter-spacing:1px}
.call{left:700px;top:64px}
.call-label{left:785px;top:66px;font-family:"Marcellus",serif;font-size:19px;color:#8a7d6a}
.call-number{left:782px;top:89px;font-family:"Marcellus",serif;font-size:25px;color:#8a7d6a}

/* nav */
.nav{left:0;top:132px;width:1000px;height:30px;background:var(--nav);display:flex;align-items:center;list-style:none}
.nav li{font-family:"Cinzel",serif;font-size:13.5px;font-weight:700;color:var(--nav-text);height:30px;line-height:30px;text-align:center;border-right:1px solid #f3ecdc}
.nav li:last-child{border-right:0}

/* hero */
.hero{left:0;top:163px;width:1000px;height:435px;background:linear-gradient(180deg,var(--hero),var(--hero-dark))}
.hero-photo{right:0;top:0;width:630px;height:435px;background:linear-gradient(115deg,rgba(216,70,42,0) 0,#e8b08e 18%,#c98b6c 34%,#2a2c36 55%,#1c1e26 80%,#6a8fbe 100%)}
.hero-card{left:610px;top:135px;width:254px;height:162px;background:#f4ecdc;display:flex;align-items:center;justify-content:center;gap:8px;box-shadow:0 2px 6px rgba(0,0,0,.3)}
.hero-card .brand-dot{width:20px;height:20px}
.hero-card .brand-name{font-size:30px}
.hero-title{left:75px;top:92px;font-family:"Cinzel Decorative",serif;font-weight:700;font-size:33px;color:var(--white);letter-spacing:1px;text-shadow:1px 2px 2px rgba(0,0,0,.35)}
.hero-lines{left:75px;top:148px;font-family:"Questrial",sans-serif;font-size:19px;line-height:22px;color:var(--white)}
.hero-btn{left:69px;top:306px;width:275px;height:40px;border-radius:20px;background:linear-gradient(180deg,#fbf6ec,#e4d9c4);box-shadow:0 2px 4px rgba(0,0,0,.35);display:flex;align-items:center;padding-left:15px;gap:10px;font-family:"Questrial",sans-serif;font-size:19px;color:#b9351c}
.hero-notch{left:895px;top:423px;width:0;height:0;border-left:12px solid transparent;border-right:12px solid transparent;border-bottom:12px solid var(--page)}

/* strip */
.strip{left:5px;top:602px;height:88px;display:flex}
.strip div{height:88px}

/* content */
.h-section{font-family:"Cinzel",serif;font-size:22px;color:var(--heading)}
.welcome-text{left:30px;top:741px;width:650px;font-size:12px;line-height:20px;color:var(--body)}
.more{color:var(--accent);font-weight:700;margin-left:12px}
.services{left:26px;top:938px;display:flex;gap:13px}
.service{width:158px;text-align:center}
.service-img{width:158px;height:80px;border:1px solid #c9bfae;padding:3px;background:var(--white)}
.service-img div{width:100%;height:100%}
.service-caption{margin-top:10px;font-size:12px;color:var(--accent)}

/* sidebar */
.sidebar{left:723px;top:692px;width:277px;height:243px;background:var(--sidebar);border-left:2px solid #d8cba8}
.news-title{left:16px;top:16px;font-family:"Marcellus",serif;font-size:22px;color:var(--heading)}
.news-item{left:10px;width:250px}
.news-date{font-size:13px;font-weight:700;color:var(--accent);letter-spacing:.5px}
.news-body{font-size:12px;line-height:18px;color:var(--body)}
.news-rule{left:10px;top:134px;width:240px;border-top:1px dotted var(--rule)}
.news-more{left:225px;top:218px;font-size:11px;font-weight:700;color:#8a7d6a}

.newsletter{left:723px;top:935px;width:277px;height:117px;background:linear-gradient(180deg,#c8321b,#a82512)}
.newsletter-title{left:22px;top:8px;font-family:"Marcellus",serif;font-size:22px;color:var(--white)}
.newsletter-input{left:20px;top:47px;width:234px;height:26px;background:#f8f2e6;font-size:11px;color:#7a6f60;line-height:26px;padding-left:11px}
.newsletter-btn{left:141px;top:82px;width:115px;height:25px;border-radius:13px;background:linear-gradient(180deg,#fbf6ec,#e1d4bd);font-size:12px;font-weight:700;color:var(--accent);line-height:25px;padding-left:24px}

/* footer */
.footer{left:0;top:1062px;width:1000px;border-top:1px solid #ddd0b2}
.footer-links{top:14px;left:0;width:1000px;display:flex;justify-content:center;font-size:12px;color:#4f473c;list-style:none}
.footer-links li{padding:0 21px;border-right:1px solid #4f473c;line-height:13px}
.footer-links li:last-child{border-right:0}
.copyright{top:47px;left:0;width:1000px;text-align:center;font-size:12px;color:#4f473c}
</style>
</head>
<body>
<div class="stage">
  <div class="page">
    <header>
      <div class="abs brand"><span class="brand-dot"></span><span class="brand-name">Carevita</span></div>
      <div class="abs brand-tag">Medical Club</div>
      <svg class="abs call" width="78" height="50" viewBox="0 0 78 50" aria-hidden="true">
        <path d="M6 14 Q39 -2 72 14 L70 22 L58 20 L56 13 Q39 8 22 13 L20 20 L8 22 Z" fill="#1e1e1e"/>
        <path d="M20 24 L58 24 L66 46 L12 46 Z" fill="#2a2a2a"/>
        <circle cx="39" cy="34" r="8" fill="#555"/>
        <circle cx="39" cy="34" r="3" fill="#ccc"/>
      </svg>
      <div class="abs call-label">Call Us</div>
      <div class="abs call-number">1800-555-0142</div>
    </header>

    <ul class="abs nav">
      <li style="width:101px">HOME</li>
      <li style="width:100px">ABOUT US</li>
      <li style="width:100px">VIP CLUB</li>
      <li style="width:97px">SERVICES</li>
      <li style="width:191px">PACKAGES AND PRICES</li>
      <li style="width:141px">REGISTRATION</li>
      <li style="width:138px">TESTIMONIALS</li>
      <li style="width:132px">CONTACTS</li>
    </ul>

    <section class="abs hero">
      <div class="abs hero-photo" role="img" aria-label="Businessman in a dark suit holding up a club membership card"></div>
      <div class="abs hero-card"><span class="brand-dot"></span><span class="brand-name">Carevita</span></div>
      <div class="abs hero-title">SOME TEXT COMES HERE</div>
      <div class="abs hero-lines">Some Text comes here<br>Some Text comes here<br>Some Text comes here</div>
      <div class="abs hero-btn">Click here to Register
        <svg width="30" height="20" viewBox="0 0 30 20" aria-hidden="true"><path d="M2 2 L11 10 L2 18 M15 2 L24 10 L15 18" fill="none" stroke="#d2381c" stroke-width="4"/></svg>
      </div>
      <div class="abs hero-notch"></div>
    </section>

    <div class="abs strip">
      <div style="width:196px;background:linear-gradient(90deg,#7a1414,#c4232a)" role="img" aria-label="Hospital emergency sign"></div>
      <div style="width:202px;background:linear-gradient(180deg,#e8a24a,#8a6a54)" role="img" aria-label="Airliner above clouds at sunset"></div>
      <div style="width:198px;background:linear-gradient(180deg,#6a5a48,#c9a86a)" role="img" aria-label="Hotel reception desk"></div>
      <div style="width:394px;background:linear-gradient(90deg,#e6e8ec,#cfd6de 55%,#22252e 80%,#5a82b2)" role="img" aria-label="Team of doctors and membership card in hand"></div>
    </div>

    <h2 class="abs h-section" style="left:28px;top:709px">WELCOME TO OUR SITE</h2>
    <p class="abs welcome-text">Lorem ipsum dolor sit amet, consectetuer adipiscing elit. Aenean commodo ligula eget dolor. Aenean massa. Cum sociis natoque penatibus et magnis dis parturient montes, nascetur ridiculus mus.Lorem ipsum dolor sit amet, consectetuer adipiscing elit. Aenean commodo ligula eget dolor. Aenean massa. Cum sociis natoque penatibus et magnis dis parturient montes, nascetur ridiculus mus.Lorem ipsum dolor sit amet, consectetuer adipiscing elit. Aenean commodo ligula eget dolor. Aenean massa. Cum sociis natoque penatibus et magnis dis parturient montes, nascetur ridiculus mus.Lorem ipsum dolor sit amet, consectetuer adipiscing elit. Aenean commodo ligula eget dolor. Aenean massa. Cum sociis natoque penatibus et magnis dis parturient montes, nascetur ridiculus mus.<span class="more">more ..</span></p>

    <h2 class="abs h-section" style="left:29px;top:899px">SERVICES</h2>
    <div class="abs services">
      <div class="service"><div class="service-img"><div style="background:linear-gradient(180deg,#f4f4f4,#d8dce0)" role="img" aria-label="Ambulance"></div></div><div class="service-caption">Lorem ipsum dolo</div></div>
      <div class="service"><div class="service-img"><div style="background:linear-gradient(90deg,#3a3028,#9fb8d6)" role="img" aria-label="Passenger looking at a plane from a window"></div></div><div class="service-caption">Lorem ipsum dolo</div></div>
      <div class="service"><div class="service-img"><div style="background:linear-gradient(90deg,#d88a3a,#6a86a8,#e0c040)" role="img" aria-label="Group of young travellers"></div></div><div class="service-caption">Lorem ipsum dolo</div></div>
      <div class="service"><div class="service-img"><div style="background:linear-gradient(90deg,#e4ecee,#7fb6b0,#e8e4f0)" role="img" aria-label="Medical staff team"></div></div><div class="service-caption">Lorem ipsum dolo</div></div>
    </div>

    <aside class="abs sidebar">
      <div class="abs news-title">Latest News</div>
      <svg class="abs" style="left:140px;top:12px" width="36" height="28" viewBox="0 0 36 28" aria-hidden="true"><rect x="2" y="2" width="32" height="24" fill="#f4f4f2" stroke="#9a9a9a"/><path d="M6 8h24M6 13h12M6 17h12M6 21h12" stroke="#9a9a9a" stroke-width="2"/><rect x="21" y="12" width="9" height="10" fill="#b8b8b8"/></svg>
      <div class="abs news-item" style="top:52px"><div class="news-date">Dec 11th</div><div class="news-body">Lorem ipsum dolor sit amet, consectetuer adipiscing elit. Aenean commodo ligula eget dolor. Aenean massa.</div></div>
      <div class="abs news-rule"></div>
      <div class="abs news-item" style="top:143px"><div class="news-date">Dec 11th</div><div class="news-body">Lorem ipsum dolor sit amet, consectetuer adipiscing elit. Aenean commodo ligula eget dolor. Aenean massa.</div></div>
      <div class="abs news-more">more ..</div>
    </aside>

    <section class="abs newsletter">
      <div class="abs newsletter-title">Newsletter</div>
      <svg class="abs" style="left:132px;top:12px" width="46" height="26" viewBox="0 0 46 26" aria-hidden="true"><rect x="1" y="1" width="44" height="24" rx="2" fill="#f6c23a"/><path d="M1 2 L23 16 L45 2" fill="none" stroke="#c8901a" stroke-width="2"/></svg>
      <div class="abs newsletter-input">Enter your e-mail here:</div>
      <div class="abs newsletter-btn">Subscribe
        <svg style="position:absolute;right:12px;top:8px" width="9" height="10" viewBox="0 0 9 10" aria-hidden="true"><path d="M0 0 L9 5 L0 10 Z" fill="#4a9ad8"/></svg>
      </div>
    </section>

    <footer class="abs footer">
      <ul class="abs footer-links">
        <li>Home</li><li>About Us</li><li>VIP Club</li><li>Services</li><li>Packages and Prices</li><li>Registration</li><li>Testimonials</li><li>Contacts</li>
      </ul>
      <div class="abs copyright">© Copyright 2009 - 2010. Your Site Name Dot Com. All Rights Reserved</div>
    </footer>
  </div>
</div>
</body>
</html>
```